Vitamin B12 Liquid Drops Label

hi, i need a label designed for my vitamin b12 drops that i am going to be selling on shopzello. the label needs to quickly capture the attention of a buyer as he or she is scrolling through the thumbnail search results on shopzello.com my brand is called nralo. i already have an example brand logo i will be using, however, i need help designing the rest of the label. attached are some examples of labels i like for other supplements.some of these examples are pink. i do not want pink. please go for a blue/green color scheme. THE DESIGN MUST BE BOLD

Target Market(s)

adults ages 30 - 64

Font styles to use
Sans Serif

Colors
0455a3
cedeed
3176b5
85acd3
cfdeed
9bcb3b
abd037
cadf82
00a990

Requirements
Must have
• - bold design
• - somewhat gender-neutral color scheme because this will be used equally by men and women
• - B12 MUST be very prominent and visible on the label
Should not have
• - it should not be "crunchy" looking

```html
<!DOCTYPE html>
<html lang="en">
<head>
<meta charset="utf-8">
<title>Nralo Vitamin B12 Drops – Packaging</title>
<link rel="stylesheet" href="https://fonts.googleapis.com/css2?family=Poppins:wght@700;800&display=swap">
<style>
  :root {
    --backdrop: #121212;
    --brand-blue: #0455a3;
    --mid-blue: #3176b5;
    --soft-blue: #85acd3;
    --pale-blue: #cedeed;
    --leaf-green: #9bcb3b;
    --lime: #abd037;
    --pale-lime: #cadf82;
    --teal: #00a990;
  }
  html, body {
    margin: 0;
    width: 1200px;
    height: 800px;
    overflow: hidden;
    background: var(--backdrop);
    font-family: "Poppins", Arial, sans-serif;
  }
  .canvas {
    position: relative;
    width: 1200px;
    height: 800px;
  }
  .carton-front {
    position: absolute;
    left: 250px;
    top: 90px;
    width: 305px;
    height: 630px;
  }
  .bottle-label {
    position: absolute;
    left: 650px;
    top: 170px;
    width: 351px;
    height: 441px;
  }
  .brand-name { font-weight: 800; }
  .label-heading { font-weight: 800; }
  .label-detail { font-weight: 700; }
</style>
</head>
<body>
<main class="canvas">

  <svg class="carton-front" viewBox="0 0 305 630" role="group" aria-label="Carton front panel">
    <rect class="carton-base" width="305" height="630" fill="var(--leaf-green)"/>
    <rect class="carton-top-band" width="305" height="40" fill="var(--mid-blue)"/>
    <polygon class="carton-lower-band" points="0,455 95,420 305,540 305,612" fill="var(--teal)"/>
    <polygon class="carton-main-band" points="0,345 305,218 305,340 0,462" fill="var(--brand-blue)"/>
    <text class="brand-name" x="20" y="290" transform="rotate(-22.6 20 290)"
          font-size="58" fill="var(--brand-blue)">NRALO</text>
    <text class="label-heading" x="22" y="410" transform="rotate(-22.6 22 410)"
          font-size="40" fill="var(--pale-lime)" letter-spacing="1">VITAMIN B12</text>
  </svg>

  <svg class="bottle-label" viewBox="0 0 195 245" role="group" aria-label="Dropper bottle label">
    <rect class="label-base" width="195" height="245" fill="var(--brand-blue)"/>
    <polygon class="label-green-panel" points="0,0 195,0 158,128 0,128" fill="var(--leaf-green)"/>
    <text class="label-heading" x="5" y="100" font-size="80" fill="var(--brand-blue)" letter-spacing="-2">B12</text>
    <text class="label-detail" x="8" y="153" font-size="13" fill="var(--pale-lime)">5000 MCG*</text>
    <text class="label-detail" x="8" y="176" font-size="14" fill="var(--pale-lime)" letter-spacing="3">METHYL</text>
    <text class="label-detail" x="8" y="193" font-size="8" fill="var(--pale-lime)" letter-spacing="3">COBAMALIN</text>
    <text class="label-detail" x="8" y="222" font-size="10" fill="var(--pale-lime)">MADE IN</text>
    <text class="label-detail" x="10" y="238" font-size="10" fill="var(--pale-lime)" letter-spacing="9">USA</text>
    <text class="brand-name" x="186" y="234" text-anchor="end" font-size="21" fill="var(--pale-lime)">NRALO</text>
  </svg>

</main>
</body>
</html>
```